Design a web site for my business - Brightline Coatings Co.

We are a family business that handles design, fabrication and installation of powder coated aluminum, stainless steel and glass products. Including handrails, privacy slat screens, electric gates and pool fencing. We are based in the Whitsundays in North Queensland and service an area from Airlie Beach to Townsville.

Target Market(s)

Domestic and commercial

Industry/Entity Type

fabrication - manufacturing

Coding

Coded - Design and coding required

Number of Pages Required

5+ page

Colors
0054AA
0677BA
7BADD7
CADEEF
E8F1F8

Requirements
Must have
• photo galleries, contact page, one page for privacy screens, balustrades, glass fencing, stainless steel handrail, powder coated aluminium handrails and pool fencing

```html
<!DOCTYPE html>
<html lang="en">
<head>
<meta charset="utf-8">
<title>Brightline Coatings Co</title>
<link href="https://fonts.googleapis.com/css2?family=Montserrat:wght@400;500;600;700;800&family=Lato:wght@400;700&display=swap" rel="stylesheet">
<style>
:root{
  --blue-deep:#0054AA;
  --blue:#0677BA;
  --blue-soft:#7BADD7;
  --blue-pale:#CADEEF;
  --blue-mist:#E8F1F8;
  --ink:#243a52;
  --muted:#4f6478;
  --white:#ffffff;
}
*{box-sizing:border-box;margin:0;padding:0}
html,body{width:1200px;height:4902px;overflow:hidden}
body{font-family:'Lato',sans-serif;color:var(--ink);background:var(--white);position:relative}
.section{position:absolute;left:0;width:1200px}
.abs{position:absolute}
.btn{position:absolute;display:flex;align-items:center;justify-content:center;border-radius:22px;background:var(--blue);color:#fff;font-size:14px;font-family:'Lato',sans-serif;white-space:nowrap}
.btn.outline{background:transparent;border:2px solid #fff}
.eyebrow{font-family:'Montserrat',sans-serif;font-size:19px;color:var(--muted);letter-spacing:.5px}
.heading{font-family:'Montserrat',sans-serif;font-weight:800;font-size:39px;line-height:44px;color:var(--blue-deep);letter-spacing:.5px}
.rule{height:3px;width:116px;background:var(--blue-soft);border-radius:2px}
.photo{position:absolute;border-radius:10px}
/* header */
.site-header{top:0;height:102px;background:#fff;border-bottom:1px solid var(--blue-pale)}
.brand{left:112px;top:28px;display:flex;align-items:center;gap:12px}
.brand .mark{width:46px;height:46px;border-radius:50%;background:var(--blue-deep)}
.brand .name{font-family:'Montserrat',sans-serif;font-weight:800;font-size:17px;color:var(--blue-deep);line-height:20px}
.nav{top:40px;font-size:15px;color:var(--ink)}
.nav.active{color:var(--blue-deep);font-weight:700}
/* hero */
.hero{top:102px;height:558px;background:linear-gradient(100deg,#003f82 0%,var(--blue-deep) 40%,var(--blue) 70%,var(--blue-soft) 100%)}
.hero h1{position:absolute;left:108px;top:92px;font-family:'Montserrat',sans-serif;color:#fff;font-size:47px;line-height:57px;font-weight:800}
.hero h1 span{font-weight:400}
.hero p{position:absolute;left:108px;top:276px;width:508px;color:#fff;font-size:24px;line-height:34px}
/* services */
.services{top:660px;height:693px}
.card-cap{position:absolute;width:230px;text-align:center;font-family:'Montserrat',sans-serif;font-size:21px;font-weight:500;color:var(--blue-deep)}
.body-copy{font-size:16px;line-height:28px;color:var(--ink)}
/* about */
.about{top:1353px;height:736px;background:var(--blue-mist)}
.center{text-align:center;width:1200px;left:0}
/* projects */
.projects{top:2089px;height:1806px}
.project{position:absolute;left:111px;width:978px;height:440px;border-radius:12px}
.project .pin{position:absolute;left:52px;top:140px;width:44px;height:44px;border-radius:50%;background:rgba(255,255,255,.92);display:flex;align-items:center;justify-content:center}
.project .loc{position:absolute;left:114px;top:152px;color:#fff;font-size:17px}
.project h3{position:absolute;left:54px;top:212px;color:#fff;font-family:'Montserrat',sans-serif;font-weight:600;font-size:23px}
.project p{position:absolute;left:54px;top:256px;width:380px;color:#fff;font-size:15px;line-height:26px}
/* why */
.why{top:3895px;height:560px;background:var(--blue-mist)}
.feature{position:absolute;top:282px;width:250px;text-align:center}
.feature .ring{width:112px;height:112px;border-radius:50%;background:var(--blue);margin:0 auto;display:flex;align-items:center;justify-content:center}
.feature h4{margin-top:28px;font-family:'Montserrat',sans-serif;font-weight:500;font-size:22px;line-height:27px;color:var(--blue-deep)}
/* footer */
.site-footer{top:4455px;height:447px;background:var(--blue-deep);color:#fff}
.site-footer h5{position:absolute;font-family:'Montserrat',sans-serif;font-weight:600;font-size:19px}
.flink{position:absolute;font-size:14px;color:#fff;white-space:nowrap}
.social{position:absolute;width:28px;height:28px;border-radius:50%;border:2px solid #fff}
</style>
</head>
<body>

<header class="section site-header">
  <div class="abs brand"><div class="mark"></div><div class="name">BRIGHTLINE<br><span style="font-weight:800;font-size:11px">COATINGS CO</span></div></div>
  <a class="abs nav active" style="left:486px">Home</a>
  <a class="abs nav" style="left:572px">About Us</a>
  <a class="abs nav" style="left:680px">Services</a>
  <a class="abs nav" style="left:780px">Projects</a>
  <a class="btn" style="left:885px;top:30px;width:204px;height:42px;font-size:15px">Request a Free Quote</a>
</header>

<section class="section hero" role="img" aria-label="Modern home with pool and glass fencing">
  <h1><span>PREMIUM ALUMINIUM,</span><br>STAINLESS STEEL &amp;<br>GLASS SOLUTIONS</h1>
  <p>Premium powder-coated fabrication, fencing and architectural metalwork by a trusted family-owned business.</p>
  <a class="btn" style="left:108px;top:413px;width:200px;height:43px">Request a Free Quote</a>
  <a class="btn outline" style="left:324px;top:413px;width:202px;height:43px">View Our Projects</a>
</section>

<section class="section services">
  <div class="abs eyebrow" style="left:111px;top:108px">OUR SERVICES</div>
  <h2 class="abs heading" style="left:111px;top:138px">ENGINEERING QUALITY.<br>CRAFTED TO LAST.</h2>
  <div class="abs rule" style="left:111px;top:238px"></div>
  <p class="abs body-copy" style="left:677px;top:104px;width:412px">Expert craftsmanship and durable finishes for every project—from fencing and gates to handrails and architectural metalwork.</p>
  <a class="btn" style="left:677px;top:215px;width:188px;height:42px">View All Services</a>
  <div class="photo" style="left:111px;top:302px;width:230px;height:228px;background:linear-gradient(180deg,#7d8b93,#3a8fc9)" role="img" aria-label="Pool ladder rails"></div>
  <div class="photo" style="left:360px;top:302px;width:230px;height:228px;background:linear-gradient(180deg,#5b89c7,#555c60 60%,#aaa)" role="img" aria-label="House with privacy screen"></div>
  <div class="photo" style="left:610px;top:302px;width:230px;height:228px;background:linear-gradient(180deg,#6e93c9,#4a5055 55%,#8c7c6c)" role="img" aria-label="Electric gate at driveway"></div>
  <div class="photo" style="left:859px;top:302px;width:230px;height:228px;background:linear-gradient(180deg,#a7b0b6,#3c4c5a)" role="img" aria-label="Powder coating spray gun"></div>
  <div class="card-cap" style="left:111px;top:546px">Pool Fencing</div>
  <div class="card-cap" style="left:360px;top:546px">Privacy Screens</div>
  <div class="card-cap" style="left:610px;top:546px">Electric Gates</div>
  <div class="card-cap" style="left:859px;top:546px">Powder Coating</div>
</section>

<section class="section about">
  <div class="abs eyebrow center" style="top:92px">ABOUT US</div>
  <h2 class="abs heading center" style="top:118px">BUILT ON QUALITY.<br>TRUSTED BY NORTH QUEENSLAND.</h2>
  <div class="abs rule" style="left:542px;top:222px"></div>
  <div class="photo" style="left:111px;top:270px;width:481px;height:372px;background:linear-gradient(160deg,#4f7d3e,#4a6fb8 50%,#9aa3a8)" role="img" aria-label="Worker installing fencing"></div>
  <div class="abs" style="left:677px;top:300px;width:412px;font-size:13.5px;line-height:25px">
    <p>Brightline Coatings Co is a family-owned business specializing in custom aluminium, stainless steel, and glass fabrication. From design and fabrication to professional installation, we create durable, high-quality solutions for residential and commercial properties.</p>
    <p style="margin-top:24px">Serving the Whitsundays and North Queensland—from Airlie Beach to Townsville—we take pride in exceptional craftsmanship, premium materials, and personalized service.</p>
  </div>
  <a class="btn" style="left:677px;top:559px;width:188px;height:42px">View All Services</a>
</section>

<section class="section projects">
  <div class="abs eyebrow" style="left:111px;top:116px">FEATURED PRODUCTS</div>
  <h2 class="abs heading" style="left:111px;top:146px">CRAFTED SOLUTIONS<br>FOR EVERY SPACE</h2>
  <div class="abs rule" style="left:111px;top:246px"></div>
  <p class="abs body-copy" style="left:677px;top:112px;width:412px">Discover our custom-built aluminium, stainless steel, and glass solutions designed to enhance the security, functionality, and style of homes and businesses.</p>
  <a class="btn" style="left:677px;top:223px;width:188px;height:42px">View All Projects</a>

  <article class="project" style="top:317px;background:linear-gradient(90deg,#1d3f5c 0%,#2f6a70 55%,#3f86b0 100%)" role="img" aria-label="Glass pool fencing by a pool">
    <div class="pin"><svg width="18" height="22" viewBox="0 0 18 22"><path d="M9 1a8 8 0 0 0-8 8c0 6 8 12 8 12s8-6 8-12a8 8 0 0 0-8-8z" fill="var(--blue)"/><circle cx="9" cy="9" r="3" fill="#fff"/></svg></div>
    <div class="loc">Airlie Beach, QLD</div>
    <h3>Premium Pool Fencing</h3>
    <p>Enhance safety and style with compliant aluminium and frameless glass pool fencing designed to complement modern outdoor spaces.</p>
    <a class="btn" style="left:50px;top:350px;width:154px;height:40px">View Project</a>
  </article>

  <article class="project" style="top:788px;background:linear-gradient(90deg,#2f3d4a 0%,#4f5d68 55%,#8b8c86 100%)" role="img" aria-label="Aluminium slat fencing by stairs">
    <div class="pin"><svg width="18" height="22" viewBox="0 0 18 22"><path d="M9 1a8 8 0 0 0-8 8c0 6 8 12 8 12s8-6 8-12a8 8 0 0 0-8-8z" fill="var(--blue)"/><circle cx="9" cy="9" r="3" fill="#fff"/></svg></div>
    <div class="loc">Cannonvale, QLD</div>
    <h3>Custom Aluminium Slat Fencing</h3>
    <p>Create privacy, security, and contemporary street appeal with durable powder-coated aluminium slat fencing.</p>
    <a class="btn" style="left:50px;top:350px;width:154px;height:40px">View Project</a>
  </article>

  <article class="project" style="top:1259px;background:linear-gradient(180deg,#1f4590 0%,#2f5aa6 55%,#55605a 100%)" role="img" aria-label="Balustrade against blue sky">
    <div class="pin"><svg width="18" height="22" viewBox="0 0 18 22"><path d="M9 1a8 8 0 0 0-8 8c0 6 8 12 8 12s8-6 8-12a8 8 0 0 0-8-8z" fill="var(--blue)"/><circle cx="9" cy="9" r="3" fill="#fff"/></svg></div>
    <div class="loc">Hamilton Island, QLD</div>
    <h3>Frameless Glass Balustrades</h3>
    <p>Precision-crafted aluminium and stainless steel handrails combining safety, durability, and modern architectural design.</p>
    <a class="btn" style="left:50px;top:350px;width:154px;height:40px">View Project</a>
  </article>
</section>

<section class="section why">
  <div class="abs eyebrow center" style="top:96px">WHY CHOOSE US</div>
  <h2 class="abs heading center" style="top:122px">CRAFTSMANSHIP YOU CAN TRUST.<br>QUALITY THAT LASTS.</h2>
  <div class="abs rule" style="left:542px;top:222px"></div>
  <div class="feature" style="left:78px"><div class="ring"><svg width="56" height="56" viewBox="0 0 56 56" fill="none" stroke="#fff" stroke-width="3"><path d="M28 46 10 28a10 10 0 0 1 18-12 10 10 0 0 1 18 12z"/></svg></div><h4>Family-Owned &amp;<br>Operated</h4></div>
  <div class="feature" style="left:329px"><div class="ring"><svg width="56" height="56" viewBox="0 0 56 56" fill="none" stroke="#fff" stroke-width="3"><rect x="10" y="10" width="36" height="36"/><path d="M16 40 40 16M16 40l4-10 6 6z"/></svg></div><h4>Fully Custom<br>Designs</h4></div>
  <div class="feature" style="left:578px"><div class="ring"><svg width="56" height="56" viewBox="0 0 56 56" fill="none" stroke="#fff" stroke-width="3"><rect x="14" y="8" width="28" height="34"/><path d="M20 18h16M20 26h16M20 34h10"/></svg></div><h4>Residential &amp;<br>Commercial Projects</h4></div>
  <div class="feature" style="left:847px"><div class="ring"><svg width="56" height="56" viewBox="0 0 56 56" fill="none" stroke="#fff" stroke-width="3"><path d="M12 20h20l6 6-6 6H12zM22 32v12M38 26h8"/></svg></div><h4>High Quality Powder<br>Coating</h4></div>
</section>

<footer class="section site-footer">
  <div class="abs" style="left:102px;top:120px;display:flex;align-items:center;gap:10px">
    <div style="width:34px;height:34px;border-radius:50%;background:#fff"></div>
    <div style="font-family:'Montserrat',sans-serif;font-weight:800;font-size:18px;line-height:20px">BRIGHTLINE<br><span style="font-size:12px">COATINGS CO</span></div>
  </div>
  <h5 style="left:405px;top:94px">Main Links</h5>
  <a class="flink" style="left:405px;top:148px">Home</a>
  <a class="flink" style="left:405px;top:186px">About Us</a>
  <a class="flink" style="left:405px;top:225px">Services</a>
  <a class="flink" style="left:405px;top:263px">Projects</a>
  <a class="flink" style="left:405px;top:302px">Our Process</a>
  <h5 style="left:603px;top:94px">Contact Us</h5>
  <svg class="abs" style="left:603px;top:148px" width="18" height="18" viewBox="0 0 24 24" fill="none" stroke="#fff" stroke-width="1.8"><path d="M5 3h4l2 5-3 2a12 12 0 0 0 6 6l2-3 5 2v4a2 2 0 0 1-2 2A18 18 0 0 1 3 5a2 2 0 0 1 2-2z"/></svg>
  <div class="flink" style="left:643px;top:151px">+61 400 555 018</div>
  <svg class="abs" style="left:603px;top:214px" width="18" height="18" viewBox="0 0 24 24" fill="none" stroke="#fff" stroke-width="1.8"><rect x="3" y="5" width="18" height="14"/><path d="m3 6 9 7 9-7"/></svg>
  <div class="flink" style="left:643px;top:215px">info@brightlinecoatings.com.au</div>
  <svg class="abs" style="left:603px;top:264px" width="18" height="22" viewBox="0 0 18 22" fill="none" stroke="#fff" stroke-width="1.6"><path d="M9 1a8 8 0 0 0-8 8c0 6 8 12 8 12s8-6 8-12a8 8 0 0 0-8-8z"/><circle cx="9" cy="9" r="3"/></svg>
  <div class="flink" style="left:643px;top:266px;line-height:25px">12 Harbour View Rd<br>Cannonvale, Queensland,<br>4802 ,Australia</div>
  <h5 style="left:946px;top:94px">Other Links</h5>
  <a class="flink" style="left:946px;top:155px">Gallery</a>
  <a class="flink" style="left:946px;top:193px">Contact</a>
  <a class="flink" style="left:946px;top:232px">Safety &amp; Quality</a>
  <a class="flink" style="left:946px;top:270px">Terms &amp; Conditions</a>
  <a class="flink" style="left:946px;top:309px">Privacy Policy</a>
  <div class="social" style="left:116px;top:300px;border-radius:6px;background:var(--blue)"></div>
  <div class="social" style="left:164px;top:300px"></div>
  <div class="social" style="left:212px;top:300px"></div>
  <div class="social" style="left:260px;top:300px"></div>
  <div class="abs" style="left:102px;top:390px;width:996px;height:1px;background:rgba(255,255,255,.25)"></div>
  <div class="abs center" style="top:406px;font-size:12px">Copyright © 2026 Brightline Coatings Co . All rights reserved.</div>
</footer>

</body>
</html>
```